Lanternfield Drinks business cards

We need a business card design for our new logo. The company is modern, progressive, professional, yet approachable. The key products are ready to drink bottles and cans of coffee based beverages.
These cards will be a critical part of the first impression made by our sales organization, business development team, and all external facing personnel.
Card can be a vertical or horizontal orientation.

Target Market(s)

Customers, suppliers, business partners

Industry/Entity Type

Business

Contact Information for Business Card

Business cards should feature Company Name and Logo.

Font styles to use
Serif

Colors

Designer to choose colors to be used in the design.

Requirements
Must have
• Strong readability of Name, phone #, mobile number and email address.
• Job title, website url, Street Address, and other details can be secondary level readability.
Nice to have
• High impact, simplistic quality design.
• Ok to utilize the 'H in the box' separate from the company name

```html
<!DOCTYPE html>
<html lang="en">
<head>
<meta charset="utf-8">
<title>Lanternfield Drinks business cards</title>
<link rel="stylesheet" href="https://fonts.googleapis.com/css2?family=Lora:wght@400;600;700&display=swap">
<style>
  :root {
    --backdrop: #3a3a3b;
    --card: #1e1e1f;
    --emboss-light: #6b6b6e;
    --orange: #e25a2c;
    --amber: #f0a22e;
    --white: #f2f2f2;
  }
  * { margin: 0; padding: 0; box-sizing: border-box; }
  html, body { width: 799px; height: 1200px; overflow: hidden; }
  body {
    background: var(--backdrop);
    font-family: "Lora", Georgia, serif;
    position: relative;
  }
  .card {
    position: absolute;
    left: 80px;
    width: 640px;
    height: 366px;
    background: var(--card);
    box-shadow: 0 14px 30px rgba(0,0,0,.45);
    overflow: hidden;
  }
  .card-front { top: 130px; }
  .card-back { top: 690px; }

  /* front */
  .front-mark {
    position: absolute;
    left: 50%; top: 50%;
    transform: translate(-50%, -50%);
    display: flex; align-items: center; gap: 18px;
    white-space: nowrap;
  }
  .front-mark .mark-square {
    width: 64px; height: 64px;
    border: 5px solid var(--emboss-light);
    flex: none;
  }
  .front-mark .mark-name {
    font-size: 30px; font-weight: 600;
    color: var(--emboss-light);
    letter-spacing: 1px;
  }

  /* back */
  .brand {
    position: absolute; left: 40px; top: 40px;
    display: flex; align-items: center; gap: 12px;
    white-space: nowrap;
  }
  .brand .mark-square {
    width: 40px; height: 40px;
    border: 4px solid var(--orange);
    flex: none;
  }
  .brand .brand-name {
    font-size: 27px; font-weight: 700;
    color: var(--orange);
    text-transform: uppercase;
    letter-spacing: 1px;
  }
  .person {
    position: absolute; right: 36px; top: 100px;
    text-align: right;
  }
  .person-name { font-size: 22px; font-weight: 600; color: var(--orange); }
  .person-title { font-size: 14px; color: var(--white); margin-top: 2px; }
  .contact {
    position: absolute; right: 36px; top: 160px;
    list-style: none; text-align: right;
    font-size: 14px; color: var(--white); line-height: 20px;
  }
  .contact li { display: flex; justify-content: flex-end; align-items: center; gap: 10px; white-space: nowrap; }
  .contact svg { width: 13px; height: 13px; fill: var(--orange); flex: none; }
  .contact .no-icon { padding-right: 23px; }
  .swoosh { position: absolute; left: 0; top: 0; width: 640px; height: 366px; }
  .website {
    position: absolute; right: 40px; bottom: 10px;
    font-size: 15px; color: var(--white);
  }
</style>
</head>
<body>
  <section class="card card-front">
    <div class="front-mark">
      <div class="mark-square"></div>
      <div class="mark-name">Lanternfield Drinks</div>
    </div>
  </section>

  <section class="card card-back">
    <svg class="swoosh" viewBox="0 0 640 366" aria-hidden="true">
      <path d="M0,250 C150,318 330,326 640,334 L640,366 L0,366 Z" fill="var(--orange)"/>
      <path d="M0,205 C160,290 330,306 640,318" fill="none" stroke="var(--amber)" stroke-width="8"/>
    </svg>

    <div class="brand">
      <div class="mark-square"></div>
      <div class="brand-name">Lanternfield Drinks</div>
    </div>

    <div class="person">
      <div class="person-name">Mara Ellison</div>
      <div class="person-title">Managing Director</div>
    </div>

    <ul class="contact">
      <li>555.201.4837
        <svg viewBox="0 0 16 16"><path d="M3 1h3l1.5 4-2 1.2a9 9 0 0 0 4.3 4.3L11 8.5l4 1.5v3a2 2 0 0 1-2 2A13 13 0 0 1 1 3a2 2 0 0 1 2-2z"/></svg></li>
      <li>555.348.9120
        <svg viewBox="0 0 16 16"><path d="M4 0h8a1 1 0 0 1 1 1v14a1 1 0 0 1-1 1H4a1 1 0 0 1-1-1V1a1 1 0 0 1 1-1zm1 2v10h6V2z"/></svg></li>
      <li>mara@lanternfielddrinks.com
        <svg viewBox="0 0 16 16"><path d="M0 3h16v10H0zm1.5 1.2L8 9l6.5-4.8V4h-13z"/></svg></li>
      <li class="no-icon">78 Harbor Lane,</li>
      <li class="no-icon">Millbrook, US 40213</li>
    </ul>

    <div class="website">www.lanternfielddrinks.com</div>
  </section>
</body>
</html>
```